Stationery Design Project

We need a stationery design for our Norwegian trucking company. We have existed for about 15 years and our 12 drivers uses relatively new vehicles to transport goods around in northern Norway. Long distance routes with fresh fish og food transport is our main operations.

We have already made alogo that's printed on our trucks. The logo and a picture of our trucks is attached. I think the logo i crappy, but since its already in use, changing it is not an option in this round. Still using a better colour scheme in the overall stationery and more interesting fonts is possible (altso in the logo).

Company details:
Name: Kjelvraket AS
Organisation nr 873 615 309
Post adress: 8642 Raudvik

I like minimalism and simplicity. I am avalibly for questions in normal GMT working hours either here or on mail: ivar@fjordlast.no

Reason: Hi. Im extending the deadline because I needed some time to find a vector file of our logo. Sorry for the inconvenience

Hi, and thanks for all your interest in the project. Some updates:

-          I have decided to commit to using one of the designs. Some designer will get the payment.

-          I have extended the deadline with 24 hours since I needed some time to find our firms vector logo (a slow Swedish man was holding me up)

-          We will not choose a design before the deadline. No need to rush.

-          We have received a lot of great design and think there is a need to specified the product we want to make:

o   Business Card for all our employers. I just need the design and will duplicate with the correct numbers and name myself. The information on should be: Logo, employer’s name, Phone number, email, website, Postal number and address. Use this as a template: logo, Leif Brattvoll, 47382066, Leif@fjordlast.no,, fjordlast.no, 8642 Raudvik. The order and placement of the information is your creative decision.

o   Stickers to put on the goods we travel. On the sticker the should be the following information: Logo, phone number, Tekst and link: Fraktæ av Kjelvraket. Ke du syns? Fjordlast.no/tilbakemelding (this means: Handled by Kjelvraket. What do you think Fjordlast.no/feedback -à the link will be a feedback form). The placement the information and size is your creative decision with some stings: we have been thinking of using Drukko for printing and see that a size about 6x6 cm, 8x5 or something like that. (with 3000 copies our budget is 200 punds). Any suggestions of other suppliers are welcome. Drukko price calculator http://www.drukkolabelhouse.co.uk/digital-litho-printing/printing-labels-tags/stickers/

o   Letterhead with logo, address, phone number and organizational number.

o   Envelopes with logo,address, phone number and organizational number.

Have a nice day.

 

 

• Using the blue colour in the logo and using a similar graphic approch.

```html
<!DOCTYPE html>
<html lang="no">
<head>
<meta charset="utf-8">
<title>Kjelvraket AS – Business Cards</title>
<link href="https://fonts.googleapis.com/css2?family=Source+Sans+3:wght@400;600;700;800&display=swap" rel="stylesheet">
<style>
  :root {
    --backdrop: #a4a6a9;
    --paper: #ffffff;
    --brand-deep: #0b4d9c;
    --brand-bright: #0a72b9;
    --ink: #3a3a3a;
    --rule: #c9c9c9;
    --web-ink: #333333;
  }
  * { margin: 0; padding: 0; box-sizing: border-box; }
  html, body { width: 1200px; height: 751px; overflow: hidden; }
  body {
    background: var(--backdrop);
    font-family: "Source Sans 3", "Myriad Pro", Arial, sans-serif;
    position: relative;
  }
  .card {
    position: absolute;
    width: 525px;
    height: 300px;
    text-align: center;
  }
  .card--front { left: 45px; top: 44px; background: var(--paper); }
  .card--back-white { left: 616px; top: 44px; background: var(--paper); border: 1px solid #8c8c8c; }
  .card--back-deep { left: 45px; top: 390px; background: var(--brand-deep); }
  .card--back-bright { left: 616px; top: 390px; background: var(--brand-bright); }

  .wordmark {
    position: absolute;
    left: 0; right: 0;
    font-weight: 800;
    font-size: 54px;
    letter-spacing: -0.5px;
    color: var(--brand-deep);
    line-height: 1;
  }
  .card--front .wordmark { top: 98px; }
  .card--back-white .wordmark { top: 163px; }
  .card--back-deep .wordmark,
  .card--back-bright .wordmark { top: 150px; color: var(--paper); }

  .holder-name {
    position: absolute;
    top: 186px; left: 0; right: 0;
    font-weight: 700;
    font-size: 19px;
    color: var(--brand-deep);
  }
  .divider {
    position: absolute;
    top: 216px; left: 42px;
    width: 442px; height: 2px;
    background: linear-gradient(90deg, transparent, var(--rule) 15%, var(--rule) 85%, transparent);
  }
  .contact-line {
    position: absolute;
    left: 0; right: 0;
    font-size: 15.5px;
    color: var(--ink);
    display: flex;
    justify-content: center;
    align-items: center;
    gap: 8px;
  }
  .contact-line--first { top: 238px; }
  .contact-line--second { top: 263px; }
  .contact-item { display: inline-flex; align-items: center; gap: 4px; }
  .contact-label { color: var(--brand-bright); }
  .icon { width: 12px; height: 12px; fill: var(--brand-bright); }

  .web-address {
    position: absolute;
    left: 0; right: 0;
    font-size: 18px;
    letter-spacing: 3.4px;
    color: var(--web-ink);
  }
  .card--back-white .web-address { top: 248px; }
  .card--back-deep .web-address,
  .card--back-bright .web-address { top: 249px; color: var(--paper); }
</style>
</head>
<body>

<section class="card card--front">
  <div class="wordmark">Kjelvraket</div>
  <div class="holder-name">Leif Brattvoll</div>
  <div class="divider"></div>
  <div class="contact-line contact-line--first">
    <span class="contact-item">
      <svg class="icon" viewBox="0 0 12 12"><path d="M3 1l2 2.5-1.2 1.3a7 7 0 0 0 3.4 3.4L8.5 7 11 9l-1.3 1.8C5.5 10.5 1.5 6.5 1.2 2.3z"/></svg>
      47382066
    </span>
    <span class="contact-item"><span class="contact-label">Org nr</span> 873 615 309</span>
  </div>
  <div class="contact-line contact-line--second">
    <span class="contact-item">
      <svg class="icon" viewBox="0 0 12 12"><path d="M1 5l5-3 5 3v5H1z"/><path d="M1 5l5 3 5-3" fill="none" stroke="#fff" stroke-width="1"/></svg>
      Leif@fjordlast.no
    </span>
    <span class="contact-item">
      <svg class="icon" viewBox="0 0 12 12"><circle cx="6" cy="6" r="5"/><path d="M1 6h10M6 1v10M3 2.5c2 2 2 5 0 7M9 2.5c-2 2-2 5 0 7" fill="none" stroke="#fff" stroke-width="0.8"/></svg>
      www.fjordlast.no
    </span>
    <span class="contact-item">
      <svg class="icon" viewBox="0 0 12 12"><path d="M1 11V5l5-3 5 3v6z"/><path d="M3 6h6M3 8h6" stroke="#fff" stroke-width="1"/></svg>
      8642 Raudvik
    </span>
  </div>
</section>

<section class="card card--back-white">
  <div class="wordmark">Kjelvraket</div>
  <div class="web-address">www.fjordlast.no</div>
</section>

<section class="card card--back-deep">
  <div class="wordmark">Kjelvraket</div>
  <div class="web-address">www.fjordlast.no</div>
</section>

<section class="card card--back-bright">
  <div class="wordmark">Kjelvraket</div>
  <div class="web-address">www.fjordlast.no</div>
</section>

</body>
</html>
```